Business Card Design Project

We are a construction company in Orange County, CA. We need a two sided business card. We would like the back to be our logo with web URL. Front should included Name, title, address, phone, fax and email address.

our address is
627 West Dorrance Blvd, Suite 308
Anaheim, CA 92718

Our logo files are attached.

Construction

```html
<!DOCTYPE html>
<html lang="en">
<head>
<meta charset="utf-8">
<title>Bravar Business Card</title>
<link rel="stylesheet" href="https://fonts.googleapis.com/css2?family=Source+Sans+3:wght@400;600;700&display=swap">
<style>
  :root {
    --backdrop: #e8e5e1;
    --paper: #ffffff;
    --slate-light: #6a6a6c;
    --slate-dark: #3f3f41;
    --brand-blue: #1f4e86;
    --ink-light: #ffffff;
    --ring: #6d6d6f;
  }
  * { margin: 0; padding: 0; box-sizing: border-box; }
  html, body {
    width: 1200px; height: 402px; overflow: hidden;
    background: var(--backdrop);
    font-family: "Source Sans 3", "Helvetica Neue", Arial, sans-serif;
  }
  .canvas { position: relative; width: 1200px; height: 402px; }
  .card {
    position: absolute; top: 60px; width: 511px; height: 293px; overflow: hidden;
  }
  .card--front { left: 58px; background: var(--paper); }
  .card--back {
    left: 631px;
    background: linear-gradient(90deg, var(--slate-light), var(--slate-dark));
  }
  .front-shape { position: absolute; inset: 0; width: 100%; height: 100%; }
  .front-brand {
    position: absolute; left: 22px; top: 112px; width: 250px;
    text-align: center;
    font-weight: 700; font-size: 46px; letter-spacing: 1px;
    color: var(--brand-blue);
  }
  .contact {
    position: absolute; right: 30px; top: 44px;
    text-align: right; color: var(--ink-light);
  }
  .contact__name { font-weight: 700; font-size: 17px; line-height: 20px; }
  .contact__title { font-size: 14px; line-height: 20px; margin-bottom: 22px; }
  .contact__line {
    display: flex; justify-content: flex-end; align-items: center; gap: 5px;
    font-size: 13px; line-height: 17px;
  }
  .contact__line svg { width: 10px; height: 10px; fill: var(--ink-light); }
  .contact__gap { height: 2px; }
  .address {
    position: absolute; right: 30px; top: 222px;
    text-align: right; color: var(--ink-light);
    font-size: 13px; line-height: 17px;
  }
  .back-brand {
    position: absolute; inset: 0;
    display: flex; align-items: center; justify-content: center; gap: 18px;
  }
  .back-brand__dot {
    width: 46px; height: 46px; border-radius: 50%; background: var(--ring);
  }
  .back-brand__name {
    font-weight: 700; font-size: 72px; letter-spacing: 2px; color: var(--ink-light);
  }
</style>
</head>
<body>
<main class="canvas">
  <section class="card card--front" aria-label="Card front">
    <svg class="front-shape" viewBox="0 0 511 293" preserveAspectRatio="none" aria-hidden="true">
      <defs>
        <linearGradient id="slate" x1="0" x2="1" y1="0" y2="0">
          <stop offset="0" stop-color="#6a6a6c"/>
          <stop offset="1" stop-color="#3f3f41"/>
        </linearGradient>
      </defs>
      <path d="M334 0 C360 60 356 110 322 160 C296 200 298 250 316 293" fill="none" stroke="#1f4e86" stroke-width="5"/>
      <path d="M342 0 C368 60 364 110 330 160 C304 200 306 250 324 293 L511 293 L511 0 Z" fill="url(#slate)"/>
      <path d="M342 0 C368 60 364 110 330 160 C304 200 306 250 324 293" fill="none" stroke="#ffffff" stroke-width="1.5"/>
    </svg>
    <div class="front-brand">BRAVAR</div>
    <div class="contact">
      <div class="contact__name">Your Name</div>
      <div class="contact__title">Title</div>
      <div class="contact__line">
        <svg viewBox="0 0 10 10"><path d="M2 0.5 L3.8 2.8 L2.8 4 C3.5 5.6 4.5 6.6 6 7.2 L7.2 6.2 L9.5 8 L8.4 9.5 C4.5 9.3 0.7 5.5 0.5 1.6 Z"/></svg>
        <span>01-234-5678</span>
      </div>
      <div class="contact__line">
        <svg viewBox="0 0 10 10"><rect x="2.5" y="0.5" width="5" height="3"/><rect x="0.5" y="3.5" width="9" height="4.5" rx="1"/><rect x="2.5" y="7" width="5" height="2.5"/></svg>
        <span>01-234-5678</span>
      </div>
      <div class="contact__gap"></div>
      <div class="contact__line">
        <svg viewBox="0 0 10 10"><path d="M0.5 2 H9.5 V8.5 H0.5 Z M1 2.5 L5 5.5 L9 2.5" stroke="#505052" stroke-width="0.6"/></svg>
        <span>info@bravarbuild.com</span>
      </div>
      <div class="contact__line">
        <svg viewBox="0 0 10 10"><circle cx="5" cy="5" r="4.5"/><path d="M0.8 5 H9.2 M5 0.6 V9.4" stroke="#505052" stroke-width="0.7"/></svg>
        <span>www.bravarbuild.com</span>
      </div>
    </div>
    <div class="address">
      627 West Dorrance Blvd<br>
      Suite 308, Anaheim<br>
      CA&nbsp; 92718
    </div>
  </section>

  <section class="card card--back" aria-label="Card back">
    <div class="back-brand">
      <span class="back-brand__dot"></span>
      <span class="back-brand__name">BRAVAR</span>
    </div>
  </section>
</main>
</body>
</html>
```